Bright Towns Forum PowerPoint Design Template and Sample Deck

The Bright Towns Forum is an international organization that seeks to improve the livability, workability and sustainability of the world’s cities.
We seek a versatile PowerPoint design template with 10 slide types plus a “self-documenting” sample deck. Your design will be used in keynote speeches and workshops around the world.
After the contest is completed, we will ask the winning designer to add 10-20 additional slide types for $75 per slide. We also seek a long-term relationship whereby we can request “custom” slides and/or ask the designer to touch up the slides we build to make them better.
FILES. We have uploaded several files:
2. PALETTE. Shows our official colors.
3 LOGOS. Several individual files with different variations of our logo. Some with our motto, some without.
2. SAMPLE SLIDES. Because we were unable to successfully upload our sample deck, we are making it available via this FileNook link:
https://www.filenook-example.com/s/k7qrtmzp2wd9hxa/The%20Bright%20Towns%20Forum%20Design%20Contest%20Notes.docx?dl=0
Target Market(s)
Mayors, department heads, CIOs, senior executives from technology companies
Industry/Entity Type
Information Technology
Colors
Designer to choose colors to be used in the design.
Requirements
Must have
- Please see uploaded Word document for requirements, nice to haves and should not haves and uploaded palette for color preferences.
Nice to have
- see above
Should not have
- see above

```html
<!DOCTYPE html>
<html lang="en">
<head>
<meta charset="utf-8">
<title>Individual Slides - 01b</title>
<link href="https://fonts.googleapis.com/css2?family=Roboto:wght@900&family=Roboto+Condensed:wght@300&family=Open+Sans:ital,wght@0,400;0,600;0,700;1,400;1,600&display=swap" rel="stylesheet">
<style>
:root{
  --page:#ffffff;
  --stage:#f3f1ec;
  --headline:#e2b9bc;
  --royal:#0b3f8e;
  --navy:#0a2d62;
  --navy-deep:#0c2a57;
  --orange:#f3a21b;
  --white:#ffffff;
  --title-blue:#1f5bb5;
  --body-grey:#8a8f98;
  --photo-grey-a:#3a3a3a;
  --photo-grey-b:#9a9a9a;
  --quote-a:#4b5277;
  --quote-b:#8b7f95;
  --skin:#e9a07a;
}
*{margin:0;padding:0;box-sizing:border-box}
html,body{width:1200px;height:1200px;overflow:hidden;background:var(--page)}
body{position:relative;font-family:"Open Sans",sans-serif}
.sheet-title{position:absolute;top:58px;left:0;width:1200px;text-align:center;font-family:"Roboto",sans-serif;font-weight:900;font-size:68px;letter-spacing:1px;color:var(--headline)}
.sheet-sub{position:absolute;top:142px;left:0;width:1200px;text-align:center;font-family:"Roboto Condensed",sans-serif;font-weight:300;font-size:29px;color:var(--headline)}
.stage{position:absolute;left:58px;top:203px;width:1058px;height:997px;background:var(--stage)}
.slide{position:absolute;width:282px;height:155px;overflow:hidden;box-shadow:0 3px 8px rgba(0,0,0,.25)}
.c1{left:120px}.c2{left:450px}.c3{left:780px}
.r1{top:232px}.r2{top:409px}.r3{top:590px}.r4{top:790px}.r5{top:967px}
.section{background:var(--royal)}
.section.dark{background:var(--navy-deep)}
.section-label{position:absolute;right:20px;top:72px;text-align:right;color:var(--white);font-size:7.5px;font-weight:700;display:flex;gap:6px;align-items:flex-start}
.section-label small{display:block;font-size:5px;font-weight:400;font-style:italic;opacity:.85}
.photo{position:absolute}
.photo-crowd{background:linear-gradient(160deg,var(--photo-grey-b),var(--photo-grey-a) 55%,#6c6c6c)}
.photo-hall{background:linear-gradient(170deg,#c9cfd6 0%,#7c8fa6 35%,#3c3f48 70%,#6b5b55)}
.photo-portrait{background:linear-gradient(110deg,var(--quote-a) 0%,var(--quote-b) 55%,var(--skin) 80%,#f0776a)}
.photo-blue{background:linear-gradient(150deg,#2d4f85,#173a70)}
.topbar{position:absolute;left:0;top:0;width:100%;height:25px;background:var(--navy);color:var(--white);font-size:9px;font-weight:600;text-align:center;line-height:25px}
.tabs{position:absolute;left:0;top:0;width:100%;height:28px;display:flex;gap:2px}
.tabs span{flex:1;background:var(--navy);color:var(--white);font-size:7px;font-weight:600;text-align:center;line-height:28px}
.footer{position:absolute;left:0;bottom:0;width:100%;height:15px;background:var(--navy);display:flex;align-items:center;justify-content:space-between;padding:0 10px}
.brand{font-size:7.5px;font-weight:600;color:var(--white)}
.footer-meta{font-size:3.5px;color:var(--white);display:flex;align-items:center;gap:3px}
.footer-meta b{display:inline-block;width:7px;height:5px;background:var(--title-blue);border-radius:1px}
.statement{position:absolute;left:0;top:40px;width:280px;text-align:center;color:var(--white);font-size:12.5px;font-weight:600;line-height:18px}
.statement em{font-style:normal;color:var(--orange)}
.quote{position:absolute;left:20px;top:22px;width:150px;color:var(--white);font-size:6.4px;font-style:italic;line-height:9.5px}
.quote em{color:var(--orange);font-weight:600}
.quote p+p{margin-top:13px}
.quote .mark{position:absolute;left:-10px;top:-4px;font-size:10px}
.quote .close{font-size:10px;margin-left:8px}
.speaker{margin-top:12px;font-style:normal;font-weight:700;font-size:5.8px;line-height:8px}
.quote-box{position:absolute;left:0;top:14px;width:180px;height:144px;background:rgba(20,40,100,.45)}
.white{background:var(--white)}
.slide-title{position:absolute;color:var(--title-blue);font-size:10px;font-weight:700;text-align:center}
.dots{display:block;font-size:7px;letter-spacing:1px;line-height:6px;color:var(--title-blue)}
.copy{position:absolute;color:var(--body-grey);font-size:2.9px;font-style:italic;line-height:5.2px}
.copy p{margin-bottom:4px}
.copy ul{list-style:none}
.copy li{margin:0 0 5px 6px;position:relative}
.copy li::before{content:"›";position:absolute;left:-5px}
.icon-grid{position:absolute;left:12px;top:80px;width:180px;display:grid;grid-template-columns:1fr 1fr;row-gap:10px}
.icon-item{display:flex;gap:4px;align-items:center}
.icon-item i{width:18px;height:18px;border-radius:50%;flex:none}
.icon-item strong{display:block;font-size:3.4px;color:var(--orange)}
.icon-item.blue strong{color:var(--title-blue)}
.icon-item span{font-size:2.6px;color:var(--body-grey)}
.ticks{position:absolute;left:208px;top:82px;width:70px;list-style:none}
.ticks li{display:flex;gap:4px;margin-bottom:8px;font-size:3.2px;color:#444}
.ticks li span{font-size:2.6px;color:var(--body-grey);display:block}
.ticks svg{flex:none}
</style>
</head>
<body>
<h1 class="sheet-title">INDIVIDUAL SLIDES - 01b</h1>
<p class="sheet-sub">(Bigger size for more details)</p>
<div class="stage"></div>

<!-- Row 1 -->
<div class="slide section r1 c1">
  <div class="section-label"><div>Full Bleed With Picture Banners<small>Slide Ideas...</small></div>
  <svg width="9" height="9" viewBox="0 0 10 10"><circle cx="5" cy="5" r="4.3" fill="none" stroke="#fff" stroke-width=".8"/><path d="M4 3l3 2-3 2z" fill="#fff"/></svg></div>
</div>
<div class="slide r1 c2">
  <div class="photo photo-crowd" style="left:0;top:0;width:282px;height:155px" role="img" aria-label="Black and white photo of people working on laptops in a busy open office"></div>
  <div class="topbar">Enter Your Slide Title Text Here</div>
</div>
<div class="slide r1 c3">
  <div class="photo photo-crowd" style="left:0;top:0;width:282px;height:155px" role="img" aria-label="Black and white photo of people working on laptops in a busy open office"></div>
  <div class="tabs"><span>Your Banner Title</span><span>Your Banner Title</span><span>Your Banner Title</span></div>
  <div class="footer"><span class="brand">Bright Towns Forum</span><span class="footer-meta">Copyright 2017 <b></b></span></div>
</div>

<!-- Row 2 -->
<div class="slide r2 c1">
  <div class="photo photo-blue" style="left:0;top:0;width:282px;height:155px" role="img" aria-label="Blue tinted photo of a busy open office with people at laptops"></div>
  <p class="statement">Citizens increasingly expect<br>their cities to be<br><em>fully digital</em></p>
</div>
<div class="slide section dark r2 c2">
  <div class="section-label"><div>3 Quotation<small>Slide Ideas...</small></div>
  <svg width="9" height="9" viewBox="0 0 10 10"><circle cx="5" cy="5" r="4.3" fill="none" stroke="#fff" stroke-width=".8"/><path d="M4 3l3 2-3 2z" fill="#fff"/></svg></div>
</div>
<div class="slide r2 c3">
  <div class="photo photo-portrait" style="left:0;top:0;width:282px;height:155px" role="img" aria-label="Portrait photo of the quoted speaker resting her chin on her hand"></div>
  <div class="quote"><span class="mark">“</span>
    <p>For those of us living in cities, we need to make sure they are smart cities. <em>Nothing else makes sense</em></p>
    <p>And nothing else is such a world-wide <em>economic opportunity</em><span class="close">”</span></p>
    <div class="speaker">Marta Velden<br>Vice President<br>Continental Assembly</div></div>
</div>

<!-- Row 3 -->
<div class="slide r3 c1">
  <div class="photo photo-portrait" style="left:0;top:0;width:282px;height:155px" role="img" aria-label="Portrait photo of the quoted speaker resting her chin on her hand"></div>
  <div class="quote" style="top:22px"><span class="mark">“</span>
    <p>For those of us living in cities, we need to make sure they are smart cities. <em>Nothing else makes sense</em></p>
    <p>And nothing else is such a world-wide <em>economic opportunity</em><span class="close">”</span></p>
    <div class="speaker">Marta Velden<br>Vice President<br>Continental Assembly</div></div>
  <div class="footer"><span class="brand">Bright Towns Forum</span><span class="footer-meta">Copyright 2017 <b></b></span></div>
</div>
<div class="slide r3 c2">
  <div class="photo photo-portrait" style="left:0;top:0;width:282px;height:155px" role="img" aria-label="Portrait photo of the quoted speaker resting her chin on her hand"></div>
  <div class="quote-box"></div>
  <div class="quote" style="left:23px;top:22px;width:140px"><span class="mark">“</span>
    <p>For those of us living in cities, we need to make sure they are smart cities. <em>Nothing else makes sense</em></p>
    <p>And nothing else is such a world-wide <em>economic opportunity</em><span class="close">”</span></p>
    <div class="speaker">Marta Velden<br>Vice President<br>Continental Assembly</div></div>
</div>

<!-- Row 4 -->
<div class="slide section r4 c1">
  <div class="section-label"><div>4 Text Heavy With Complimentary Picture<small>Slide Ideas...</small></div>
  <svg width="9" height="9" viewBox="0 0 10 10"><circle cx="5" cy="5" r="4.3" fill="none" stroke="#fff" stroke-width=".8"/><path d="M4 3l3 2-3 2z" fill="#fff"/></svg></div>
</div>
<div class="slide white r4 c2">
  <div class="slide-title" style="left:0;top:5px;width:282px">Your Slide Title Here<span class="dots">•••••</span></div>
  <div class="copy" style="left:14px;top:34px;width:130px"><p>Short sample text for this slide goes here in plain words.</p></div>
  <div class="icon-grid">
    <div class="icon-item"><i style="background:#e94b2c"></i><div><strong>Your Title Here</strong><span>Short line of text</span></div></div>
    <div class="icon-item blue"><i style="background:#9a9a9a"></i><div><strong>Your Title Here</strong><span>Short line of text</span></div></div>
    <div class="icon-item"><i style="background:var(--orange)"></i><div><strong>Your Title Here</strong><span>Short line of text</span></div></div>
    <div class="icon-item blue"><i style="background:#5b8fd6"></i><div><strong>Your Title Here</strong><span>Short line of text</span></div></div>
  </div>
  <div class="photo photo-hall" style="left:162px;top:29px;width:117px;height:104px" role="img" aria-label="Photo of an audience in a conference hall facing a projection screen"></div>
  <div class="footer"><span class="brand">Bright Towns Forum</span><span class="footer-meta">Copyright 2017 <b></b></span></div>
</div>
<div class="slide white r4 c3">
  <div class="slide-title" style="left:0;top:5px;width:282px">Your Slide Title Here<span class="dots">•••••</span></div>
  <div class="copy" style="left:14px;top:34px;width:140px">
    <p>Short sample text for this slide goes here in plain words.</p>
    <p>Short sample text for this slide goes here in plain words.</p>
    <ul><li>Point text goes here in one line.</li><li>Point text goes here in one line.</li><li>Point text goes here in one line.</li></ul></div>
  <div class="photo photo-crowd" style="left:162px;top:29px;width:117px;height:104px" role="img" aria-label="Black and white photo of people working on laptops in an open office"></div>
  <div class="footer"><span class="brand">Bright Towns Forum</span><span class="footer-meta">Copyright 2017 <b></b></span></div>
</div>

<!-- Row 5 -->
<div class="slide white r5 c1">
  <div class="slide-title" style="left:0;top:5px;width:132px">Your Slide Title Here<span class="dots">•••••</span></div>
  <div class="copy" style="left:14px;top:34px;width:115px">
    <p>Short sample text for this slide goes here in plain words.</p>
    <p>Short sample text for this slide goes here in plain words.</p>
    <ul><li>Point text goes here in one line.</li><li>Point text goes here in one line.</li><li>Point text goes here in one line.</li></ul></div>
  <div class="photo photo-hall" style="left:132px;top:0;width:150px;height:140px" role="img" aria-label="Photo of an audience in a conference hall facing a projection screen"></div>
  <div class="footer"><span class="brand">Bright Towns Forum</span><span class="footer-meta">Copyright 2017 <b></b></span></div>
</div>
<div class="slide white r5 c2">
  <div class="slide-title" style="left:0;top:5px;width:132px">Your Slide Title Here<span class="dots">•••••</span></div>
  <div class="copy" style="left:14px;top:34px;width:115px">
    <p>Short sample text for this slide goes here in plain words.</p>
    <p>Short sample text for this slide goes here in plain words.</p>
    <ul><li>Point text goes here in one line.</li><li>Point text goes here in one line.</li><li>Point text goes here in one line.</li></ul></div>
  <div class="photo photo-crowd" style="left:132px;top:0;width:150px;height:155px" role="img" aria-label="Black and white photo of people working on laptops in an open office"></div>
</div>
<div class="slide white r5 c3">
  <div class="photo photo-hall" style="left:0;top:0;width:150px;height:155px" role="img" aria-label="Photo of an audience in a conference hall facing a projection screen"></div>
  <div class="slide-title" style="left:150px;top:5px;width:132px">Your Slide Title Here<span class="dots">•••••</span></div>
  <div class="copy" style="left:162px;top:34px;width:112px">
    <p>Short sample text for this slide goes here in plain words.</p>
    <p>Short sample text for this slide goes here in plain words.</p></div>
  <ul class="ticks" style="left:208px">
    <li><svg width="6" height="6" viewBox="0 0 10 10"><circle cx="5" cy="5" r="5" fill="#3aa757"/><path d="M2.7 5.2l1.6 1.6 3-3.2" fill="none" stroke="#fff" stroke-width="1.3"/></svg><div>Enter Your Title Here<span>Short line of text</span></div></li>
    <li><svg width="6" height="6" viewBox="0 0 10 10"><circle cx="5" cy="5" r="5" fill="#3aa757"/><path d="M2.7 5.2l1.6 1.6 3-3.2" fill="none" stroke="#fff" stroke-width="1.3"/></svg><div>Enter Your Title Here<span>Short line of text</span></div></li>
    <li><svg width="6" height="6" viewBox="0 0 10 10"><circle cx="5" cy="5" r="5" fill="#3aa757"/><path d="M2.7 5.2l1.6 1.6 3-3.2" fill="none" stroke="#fff" stroke-width="1.3"/></svg><div>Enter Your Title Here<span>Short line of text</span></div></li>
    <li><svg width="6" height="6" viewBox="0 0 10 10"><circle cx="5" cy="5" r="5" fill="#3aa757"/><path d="M2.7 5.2l1.6 1.6 3-3.2" fill="none" stroke="#fff" stroke-width="1.3"/></svg><div>Enter Your Title Here<span>Short line of text</span></div></li>
  </ul>
</div>
</body>
</html>
```